Single-sided business card for restaurant velmora with new logo made on this site

Business card options with new logo including restaurant name, address, phone number and website. This business card is single-sided only and will be presented at the hostess desk for clients to take. I would like to see options based on a cream card background, a white card background, a yellow card background and a burgundy colored background. It needs to be elegant and traditional.

Target Market(s)

local and international crowd

Industry/Entity Type

restaurant

Contact Information for Business Card

address, website and phone number

Font styles to use
Serif

Colors
EE7325
F08F49
F5BC92
FAE3D3
FDF4ED

Requirements
Must have
• new logo, address, phone number, website
Should not have
• more than three colors

```html
<!DOCTYPE html>
<html lang="es">
<head>
<meta charset="utf-8">
<title>Velmora – Tarjeta de presentación</title>
<link href="https://fonts.googleapis.com/css2?family=Tinos:wght@400;700&display=swap" rel="stylesheet">
<style>
  :root {
    --backdrop: #d9d9d9;
    --card-cream: #fcecd2;
    --card-edge: #f0a928;
    --brand-gold: #f2ae2e;
    --ink-brown: #3a1e1a;
    --ink-text: #2e2a28;
    --leaf-tone: #e4d5b8;
  }
  * { box-sizing: border-box; margin: 0; padding: 0; }
  html, body {
    width: 1200px; height: 800px; overflow: hidden;
    background: var(--backdrop);
  }
  .stage {
    position: relative; width: 1200px; height: 800px;
    display: flex; align-items: center; justify-content: center;
  }
  .business-card {
    position: relative; width: 960px; height: 560px;
    background: var(--card-cream);
    border-radius: 40px;
    border-bottom: 5px solid var(--card-edge);
    box-shadow: 0 18px 40px rgba(0,0,0,.18);
    overflow: hidden;
    font-family: "Tinos", "Times New Roman", serif;
    color: var(--ink-text);
  }
  .leaf-decoration {
    position: absolute; left: 0; bottom: 0; width: 640px; height: 400px;
    background: radial-gradient(ellipse 60% 70% at 45% 100%, var(--leaf-tone) 0%, rgba(228,213,184,.55) 55%, rgba(252,236,210,0) 100%);
  }
  .brand {
    position: absolute; right: 150px; top: 50px;
    display: flex; flex-direction: column; align-items: center; gap: 22px;
  }
  .brand-square {
    width: 150px; height: 150px; background: var(--brand-gold);
  }
  .brand-name {
    font-weight: 400; font-size: 58px; letter-spacing: 12px;
    color: var(--ink-brown); line-height: 1;
  }
  .contact {
    position: absolute; right: 60px; top: 360px; text-align: right;
    font-size: 30px; line-height: 1.1;
  }
  .contact-label { font-weight: 700; font-size: 28px; }
  .contact-phone { display: flex; align-items: center; justify-content: flex-end; gap: 6px; }
  .contact-phone svg { width: 24px; height: 24px; }
  .contact-web { font-size: 26px; }
  .address {
    position: absolute; left: 70px; bottom: 75px;
    font-size: 28px; line-height: 1.15;
  }
  .address-name { font-weight: 700; }
</style>
</head>
<body>
  <main class="stage">
    <article class="business-card">
      <div class="leaf-decoration" role="img" aria-label="Faint large leaf motif in soft beige"></div>

      <header class="brand">
        <div class="brand-square"></div>
        <h1 class="brand-name">VELMORA</h1>
      </header>

      <section class="contact">
        <p class="contact-label">Reservaciones</p>
        <p class="contact-phone">
          <svg viewBox="0 0 24 24" aria-hidden="true"><path d="M6.6 10.8a15.1 15.1 0 0 0 6.6 6.6l2.2-2.2a1 1 0 0 1 1-.25 11.4 11.4 0 0 0 3.6.57 1 1 0 0 1 1 1V20a1 1 0 0 1-1 1A17 17 0 0 1 3 4a1 1 0 0 1 1-1h3.5a1 1 0 0 1 1 1c0 1.25.2 2.45.57 3.57a1 1 0 0 1-.25 1z" fill="none" stroke="#2e2a28" stroke-width="1.6"/></svg>
          555-014-2290
        </p>
        <p class="contact-web">www.velmora.com.mx</p>
      </section>

      <address class="address" style="font-style:normal">
        <p class="address-name">Restaurant Velmora</p>
        <p>Calle Jazmín 417, Bahías del Sol</p>
        <p>Oaxaca CP 70412</p>
      </address>
    </article>
  </main>
</body>
</html>
```